Aquatic View

We need a web design for a new window cleaning company name Tidewell Glass Care. We are located in Grand Cayman, Cayman Islands. We are a small company, a team of husband and wife. Our services include residencial interior and exterior window cleaning and commercial. Extra services such as ceiling fans cleaning, mirrors, high dusting. Home cleaning services. Power washing. Explaining the service. We want a modern, beachy style with aquatic colors. We want to use our domain name "tidewellglasscare.ky". We want to portray a clean, modern and professional design.

Target Market(s)

Big Home owners

Industry/Entity Type

Cleaning Service

Contact Information for Business Card

Company Name: Tidewell Glass Care
Name: Desmond Farrowby owner/manager
Phone: 345-9170452
Email: desmond@tidewellglasscare.ky
Website: tidewellglasscare.ky
Address: P.O.Box 2486 GT, George Town, Grand Cayman KY1-1203 Cayman Islands

Number of Pages Required

2 page

Font styles to use
Sans Serif

Colors
0592cd
0455a3
33a6d7
85cae6
cadf82
abd036
fbf289

Requirements
Nice to have
• Pictures of an ocean view and palm trees from clear windows.
• https://quorvantel.com/bidlinker/
• Use the above for "free estimate".

```html
<!DOCTYPE html>
<html lang="en">
<head>
<meta charset="utf-8">
<title>Tidewell Glass Care</title>
<link href="https://fonts.googleapis.com/css2?family=Lato:ital,wght@0,400;0,700;0,900;1,400&display=swap" rel="stylesheet">
<style>
:root{
  --ink:#2f2f2f;
  --dark:#333333;
  --blue:#0a8fd0;
  --navy:#0455a3;
  --red:#c0141a;
  --text:#666666;
  --line:#dddddd;
  --white:#ffffff;
}
*{box-sizing:border-box;margin:0;padding:0}
html,body{width:1200px;height:1001px;overflow:hidden}
body{position:relative;font-family:'Lato',sans-serif;background:#ececec;color:var(--text)}
.topbar{position:absolute;left:0;top:0;width:1200px;height:36px;background:var(--dark)}
.topbar-phone{position:absolute;right:116px;top:5px;display:flex;align-items:center;gap:7px;color:var(--white);font-size:19px;font-weight:700;white-space:nowrap}
.header{position:absolute;left:0;top:36px;width:1200px;height:67px;background:var(--white)}
.brand{position:absolute;left:120px;top:46px;display:flex;align-items:center;gap:8px;font-size:17px;font-weight:900;color:var(--ink);white-space:nowrap}
.brand-dot{width:22px;height:22px;border-radius:50%;background:var(--blue)}
.nav{position:absolute;left:0;top:0;width:1200px;height:103px;font-size:13px;font-weight:700;color:var(--ink)}
.nav a{position:absolute;top:62px;height:22px;line-height:22px;color:inherit;text-decoration:none;white-space:nowrap}
.nav a.active{left:728px;width:66px;text-align:center;color:var(--blue);border:1px solid var(--blue);line-height:20px}
.nav .div{position:absolute;top:65px;width:1px;height:17px;background:#ccc}
.hero{position:absolute;left:0;top:103px;width:1200px;height:441px;background:linear-gradient(100deg,#a9a9a4 0%,#d7d5cd 30%,#b7c5d6 55%,#e8e6df 80%,#b9b3a6 100%)}
.hero-caption{position:absolute;left:97px;top:130px;width:367px;height:134px;background:rgba(255,255,255,.55);border-radius:3px;padding:12px 0 0 19px;font-size:25px;font-weight:700;line-height:36px;color:#333;white-space:nowrap}
.hero-arrow{position:absolute;top:195px;width:38px;height:38px;border-radius:50%;background:rgba(255,255,255,.75);box-shadow:0 0 3px rgba(0,0,0,.3)}
.hero-arrow.prev{left:32px}.hero-arrow.next{left:1128px}
.hero-arrow svg{position:absolute;left:12px;top:11px}
.content{position:absolute;left:99px;top:506px;width:1002px;height:330px;background:var(--white)}
.col{position:absolute;top:26px}
.col h2{font-size:16px;font-weight:900;letter-spacing:.4px;color:var(--blue);padding-bottom:14px;border-bottom:1px solid var(--line);position:relative;white-space:nowrap}
.col h2 span{color:var(--red)}
.col h2::after{content:"";position:absolute;left:0;bottom:-2px;width:86px;height:3px;background:var(--navy)}
.col p{font-size:13px;line-height:17px;color:var(--text)}
.about{left:17px;width:265px}
.about-photo{margin-top:14px;width:265px;height:121px;border:1px solid #ccc;background:linear-gradient(90deg,#7b93ad,#cfdbe6 55%,#9aa9b3)}
.about p{margin:10px 2px 0;line-height:19.5px}
.btn{display:inline-block;background:linear-gradient(#1b7fc4,var(--navy));color:var(--white);font-size:13px;font-weight:700;padding:0 9px;height:31px;line-height:31px;margin-top:9px;white-space:nowrap}
.sep{position:absolute;top:36px;width:1px;height:280px;background:#eee}
.services{left:334px;width:334px}
.services p{margin:11px 2px 0}
.svc h3{display:flex;align-items:center;gap:7px;font-size:15px;font-weight:700;color:var(--blue);margin-top:8px}
.svc p{margin-top:2px}
.inquiry{left:718px;width:265px}
.inquiry .pager{position:absolute;right:12px;top:4px;color:#444;font-size:14px;letter-spacing:6px}
.field{margin-top:7px;height:30px;border:1px solid #ccc;font-size:12px;color:#666;padding:6px 6px}
.inquiry .field:first-of-type{margin-top:16px}
.field.msg{height:73px}
.inquiry .btn{padding:0 20px;margin-top:9px}
.footer{position:absolute;left:0;top:855px;width:1200px;height:107px;background:var(--dark);color:var(--white)}
.f-nav{position:absolute;left:117px;top:21px;font-size:13px;font-weight:700;display:flex;white-space:nowrap}
.f-nav span.sepbar{margin:0 13px}
.f-line{position:absolute;left:116px;display:flex;align-items:center;gap:8px;font-size:13.5px;white-space:nowrap}
.subscribe{position:absolute;left:841px;top:19px;display:flex;height:30px}
.subscribe .in{width:159px;background:var(--white);border-radius:3px 0 0 3px;font-size:11px;font-style:italic;color:#888;display:flex;align-items:center;gap:7px;padding-left:8px;white-space:nowrap}
.subscribe .go{width:84px;background:#1274c0;font-size:12.5px;font-weight:700;display:flex;align-items:center;justify-content:center}
.social{position:absolute;left:968px;top:67px;display:flex;gap:7px}
.social span{width:24px;height:24px;border:1.5px solid #ddd;border-radius:50%}
.copyright{position:absolute;left:0;top:962px;width:1200px;height:39px;background:linear-gradient(#1684c8,#0a5fa8);color:var(--white);font-size:13px;text-align:center;line-height:40px}
</style>
</head>
<body>
<div class="topbar">
  <div class="topbar-phone">
    <svg width="26" height="26" viewBox="0 0 26 26"><circle cx="13" cy="13" r="12" fill="none" stroke="#fff" stroke-width="1.5"/><path d="M9 7c1 0 2 2.5 2 3s-1 1-1 1.5 2.5 3.5 3.5 3.5c.5 0 1-1 1.5-1s3 1 3 2-1.5 2.5-3 2.5C11 18.5 7.5 13 7.5 10 7.5 8 8.5 7 9 7z" fill="#fff"/></svg>
    345-917-0452
  </div>
</div>
<div class="header"></div>
<div class="brand"><span class="brand-dot"></span>Tidewell Glass Care</div>
<nav class="nav">
  <a class="active" href="#">HOME</a>
  <a href="#" style="left:811px">ABOUT US</a>
  <span class="div" style="left:888px"></span>
  <a href="#" style="left:903px">SERIVCES</a>
  <span class="div" style="left:982px"></span>
  <a href="#" style="left:1002px">CONTACT US</a>
</nav>

<section class="hero" role="img" aria-label="Smiling cleaner in yellow gloves holding a spray bottle and sponge in a bright kitchen">
  <div class="hero-caption">WE ARE<br>RESIDENTIAL,COMMERCIAL<br>CLEANING SERVICE FIRM</div>
  <span class="hero-arrow prev"><svg width="12" height="16" viewBox="0 0 12 16"><path d="M9 2 3 8l6 6" fill="none" stroke="#555" stroke-width="3"/></svg></span>
  <span class="hero-arrow next"><svg width="12" height="16" viewBox="0 0 12 16"><path d="M3 2l6 6-6 6" fill="none" stroke="#555" stroke-width="3"/></svg></span>
</section>

<main class="content">
  <section class="col about">
    <h2><span>ABOUT</span> TIDEWELL GLASS CARE</h2>
    <div class="about-photo" role="img" aria-label="Worker in blue uniform squeegeeing a large window"></div>
    <p>Lorem ipsum dolor sit amet, consectetuer adip iscing elit, sed diam nonummy nibh euismod magna aliquam erat volutpat.</p>
    <span class="btn">READ MORE</span>
  </section>
  <div class="sep" style="left:308px"></div>
  <section class="col services">
    <h2><span>OUR</span> SERVICES</h2>
    <p>Lorem ipsum dolor sit amet, consectetuer adip iscing elit sed diam nonummy nibh euismod magna.</p>
    <div class="svc">
      <h3><svg width="20" height="17" viewBox="0 0 20 17"><path d="M10 1 1 8h3v8h12V8h3z" fill="#555"/><rect x="8" y="10" width="4" height="6" fill="#fff"/></svg>Residential</h3>
      <p>Lorem ipsum dolor sit amet, consectetuer adip iscing elit sed diam nonummy nibh euismod magna.</p>
    </div>
    <div class="svc">
      <h3><svg width="20" height="18" viewBox="0 0 20 18"><path d="M1 18V8h5V2h8v6h5v10z" fill="#555"/><g fill="#fff"><rect x="8" y="4" width="1.5" height="2"/><rect x="10.5" y="4" width="1.5" height="2"/><rect x="3" y="10" width="1.5" height="2"/><rect x="15.5" y="10" width="1.5" height="2"/><rect x="8" y="9" width="1.5" height="2"/><rect x="10.5" y="9" width="1.5" height="2"/></g></svg>Commercial</h3>
      <p>Lorem ipsum dolor sit amet, consectetuer adip iscing elit sed diam nonummy nibh euismod magna.</p>
    </div>
    <div class="svc">
      <h3><svg width="20" height="18" viewBox="0 0 20 18"><circle cx="7" cy="7" r="5" fill="none" stroke="#555" stroke-width="3" stroke-dasharray="2.5 1.5"/><circle cx="15" cy="14" r="3" fill="none" stroke="#555" stroke-width="2.5" stroke-dasharray="2 1.2"/></svg>Extra Services</h3>
      <p>Lorem ipsum dolor sit amet, consectetuer adip iscing elit sed diam nonummy nibh euismod magna.</p>
    </div>
  </section>
  <div class="sep" style="left:693px"></div>
  <section class="col inquiry">
    <h2><span>QUICK</span> INQUIRY</h2>
    <span class="pager">‹›</span>
    <div class="field">Email</div>
    <div class="field">Phone</div>
    <div class="field">Email</div>
    <div class="field msg">Message</div>
    <span class="btn">SUBMIT</span>
  </section>
</main>

<footer class="footer">
  <div class="f-nav"><span>Home</span><span class="sepbar">I</span><span>About Us</span><span class="sepbar">I</span><span>Serivces</span><span class="sepbar">I</span><span>Contact Us</span></div>
  <div class="f-line" style="top:51px"><svg width="12" height="15" viewBox="0 0 12 15"><path d="M6 0a5 5 0 0 1 5 5c0 4-5 10-5 10S1 9 1 5a5 5 0 0 1 5-5z" fill="#bbb"/><circle cx="6" cy="5" r="2" fill="#333"/></svg>Lorem ipsum dolor sit amet consectetuer adimpisciged</div>
  <div class="f-line" style="top:74px"><svg width="16" height="16" viewBox="0 0 26 26"><circle cx="13" cy="13" r="12" fill="none" stroke="#bbb" stroke-width="2"/><path d="M9 7c1 0 2 2.5 2 3s-1 1-1 1.5 2.5 3.5 3.5 3.5c.5 0 1-1 1.5-1s3 1 3 2-1.5 2.5-3 2.5C11 18.5 7.5 13 7.5 10 7.5 8 8.5 7 9 7z" fill="#bbb"/></svg>345-917-0453 <svg width="11" height="8" viewBox="0 0 11 8" style="margin-left:4px"><rect width="11" height="8" fill="#bbb"/><path d="M0 0l5.5 4L11 0" fill="none" stroke="#333"/></svg>info@tidewellglasscare.ky</div>
  <div class="subscribe">
    <div class="in"><svg width="15" height="10" viewBox="0 0 15 10"><rect x=".5" y=".5" width="14" height="9" fill="none" stroke="#bbb"/><path d="M.5.5l7 5 7-5" fill="none" stroke="#bbb"/></svg>your e-mail address</div>
    <div class="go">SUBSCRIBE</div>
  </div>
  <div class="social"><span></span><span></span><span></span><span></span></div>
</footer>
<div class="copyright">Copyright © 2015&nbsp; TidewellGlassCare. All Right Reserved</div>
</body>
</html>
```